Transform Your Giving

I need a tri-fold brochure that will fit in a standard number 10 business envelope. Meadowlark and Allied Services is a charitable nonprofit. The goal of this brochure is to stimulate people into thinking about other ways to make a donation. The design should communicate the essential information on donation options, create a sense of professional integrity, be graphically sharp, easy to read and laid out in a way that doesn't make the material appear crowded.

```html
<!DOCTYPE html>
<html lang="en">
<head>
<meta charset="utf-8">
<title>Transform Your Giving – Meadowlark and Allied Services</title>
<link href="https://fonts.googleapis.com/css2?family=Montserrat:wght@500;700;800;900&family=Open+Sans:wght@400;600;700&display=swap" rel="stylesheet">
<style>
:root{
  --navy:#2f2a7c;
  --navy-deep:#241f66;
  --green:#7cc242;
  --green-dark:#5ea52c;
  --ink:#2b2b3a;
  --muted:#5b5b6b;
  --paper:#ffffff;
  --backdrop:#eef0f3;
}
*{box-sizing:border-box;margin:0;padding:0}
html,body{width:1200px;height:2700px;overflow:hidden;background:var(--backdrop)}
body{font-family:"Open Sans",Arial,sans-serif;color:var(--ink);position:relative}
.spread{position:absolute;left:50px;width:1100px;height:850px;display:flex;background:var(--paper);box-shadow:0 6px 24px rgba(0,0,0,.12);overflow:hidden}
.spread--outside{top:333px}
.spread--inside{top:1516px}
.panel{position:relative;width:366.67px;height:850px;overflow:hidden;padding:34px 30px}
.panel--navy{background:var(--navy);color:#fff}
h2,h3,h4{font-family:"Montserrat",Arial,sans-serif}
.section-title{font-size:17px;font-weight:800;color:var(--navy);letter-spacing:.3px;margin-bottom:10px}
.section-title span{color:var(--green)}
p{font-size:10.5px;line-height:1.55;margin-bottom:8px}
.panel--navy p{color:#e6e5f5}
.option-list{list-style:none;margin-top:10px}
.option-list li{display:flex;align-items:center;gap:10px;font-family:"Montserrat",Arial,sans-serif;font-weight:700;font-size:12px;color:var(--navy);padding:6px 0;border-bottom:1px solid #e3e3ee}
.option-list .dot{width:22px;height:22px;border-radius:50%;background:var(--green);display:flex;align-items:center;justify-content:center}
.photo{position:absolute;left:0;right:0;bottom:0}
.photo--care{height:380px;background:linear-gradient(160deg,#b9c8d8,#8aa0b4 55%,#d8c8b8)}
.photo--walk{height:330px;background:linear-gradient(160deg,#c9d6c0,#9bb08e 50%,#d6cbb5)}
.corner{position:absolute;width:0;height:0}
.corner--br{right:0;bottom:0;border-left:90px solid transparent;border-bottom:90px solid var(--green)}
.corner--tl{left:0;top:0;border-right:70px solid transparent;border-top:70px solid var(--green)}
.brand{display:flex;align-items:center;gap:8px;justify-content:center}
.brand__mark{width:16px;height:16px;border-radius:50%;background:var(--green)}
.brand__name{font-family:"Montserrat",Arial,sans-serif;font-weight:800;font-size:28px;color:var(--navy);letter-spacing:1px}
.panel--navy .brand__name{color:#fff}
.brand__sub{text-align:center;font-size:8px;letter-spacing:1px;text-transform:uppercase;margin-top:2px}
.lead{text-align:center;font-size:10.5px;margin-top:14px}
.lead strong{color:var(--green)}
.name-card{background:#fff;color:var(--navy);text-align:center;font-family:"Montserrat",Arial,sans-serif;font-weight:800;font-size:12px;padding:7px;margin:10px 0;letter-spacing:.5px}
.url-line{text-align:center;font-weight:700;font-size:14px;color:var(--green);margin:6px 0}
.contact-band{position:absolute;left:0;right:0;bottom:0;height:400px;background:var(--navy-deep);padding:0 30px 20px}
.contact-band__head{background:var(--green);color:#fff;font-family:"Montserrat",Arial,sans-serif;font-weight:900;font-size:22px;text-align:center;padding:10px;margin:0 -30px 14px}
.contact-band h4{text-align:center;font-size:15px;font-weight:800;margin-bottom:6px}
.contact-row{display:flex;align-items:center;gap:10px;font-size:10.5px;color:#e6e5f5;margin:10px 0}
.icon{flex:none;width:26px;height:26px;border-radius:50%;background:var(--green);display:flex;align-items:center;justify-content:center}
.follow{text-align:center;font-weight:700;font-size:11px;margin-top:12px}
.social{display:flex;justify-content:center;gap:8px;margin-top:6px}
.social span{width:20px;height:20px;border-radius:50%;background:#fff}
.cover-title{text-align:center;font-family:"Montserrat",Arial,sans-serif;font-weight:900;font-size:30px;line-height:1.05;color:var(--navy)}
.cover-title span{color:var(--green);display:block}
.cover-rule{height:3px;background:var(--green);width:140px;margin:14px auto}
.cover-strap{text-align:center;font-family:"Montserrat",Arial,sans-serif;font-weight:900;font-size:32px;line-height:1.05;color:var(--navy)}
.cover-strap span{color:var(--green)}
.cover-sub{text-align:center;font-size:14px;line-height:1.4;font-weight:600;color:var(--navy);margin-top:12px}
.cover-photo{position:absolute;left:0;right:0;top:380px;height:270px;background:linear-gradient(160deg,#9fb4c6,#6f879c 55%,#c4b6a4);clip-path:polygon(0 22%,50% 0,100% 22%,100% 100%,0 100%)}
.cover-foot{position:absolute;left:0;right:0;bottom:0;height:200px;text-align:center;padding-top:40px}
.cover-foot .web{font-family:"Montserrat",Arial,sans-serif;font-weight:800;font-size:18px;color:var(--navy);margin-top:26px}
.topic{display:flex;gap:10px;align-items:flex-start;margin:4px 0 8px}
.topic .badge{flex:none;width:34px;height:34px;background:var(--green);border-radius:6px}
.topic h3{font-size:13px;font-weight:800;line-height:1.2;color:var(--navy)}
.panel--navy .topic h3{color:#fff}
.topic h3 small{display:block;font-size:10px;color:var(--green);font-weight:700;margin-top:2px}
.how{font-family:"Montserrat",Arial,sans-serif;font-size:12px;font-weight:800;color:var(--navy);margin:6px 0 4px}
.panel--navy .how{color:var(--green)}
.ticks{list-style:none;margin-bottom:8px}
.ticks li{font-size:10.5px;line-height:1.5;padding-left:14px;position:relative;margin-bottom:4px}
.ticks li::before{content:"";position:absolute;left:0;top:5px;width:7px;height:7px;background:var(--green);border-radius:50%}
.web-foot{position:absolute;left:0;right:0;bottom:24px;text-align:center;font-family:"Montserrat",Arial,sans-serif;font-weight:800;font-size:15px;color:#fff}
.divider{height:1px;background:rgba(255,255,255,.25);margin:10px 0}
.brand-foot{position:absolute;left:0;right:0;bottom:40px}
</style>
</head>
<body>

<!-- Outside of the brochure -->
<section class="spread spread--outside">
  <article class="panel panel--impact">
    <h2 class="section-title">THE IMPACT <span>OF YOUR GIFT</span></h2>
    <p>Your generosity drives our mission. With every smart gift you're supporting Meadowlark and Allied Services, and our community of donors helps older adults live safely with dignity. Begin your smart giving journey with us today.</p>
    <ul class="option-list">
      <li><span class="dot"></span>Crypto</li>
      <li><span class="dot"></span>DAF's</li>
      <li><span class="dot"></span>Stocks &amp; Securities</li>
      <li><span class="dot"></span>QCDs</li>
      <li><span class="dot"></span>Charitable Annuity</li>
    </ul>
    <div class="photo photo--care" role="img" aria-label="Caregiver smiling beside an older man in a wheelchair"></div>
    <div class="corner corner--br"></div>
  </article>

  <article class="panel panel--navy panel--contact">
    <div class="brand"><span class="brand__mark"></span><span class="brand__name">MAAS</span></div>
    <p class="brand__sub">Meadowlark and Allied Services</p>
    <p class="lead">To learn more about including Meadowlark and Allied Services in your will, please reach out to our team. <strong>We are here to help you navigate these giving methods and answer any questions you may have.</strong></p>
    <p class="lead">Planning a gift? Reference a copy of our giving guide and contact</p>
    <div class="name-card">DANIEL WHITCOMBE</div>
    <p class="lead">If you do not have a will, go to</p>
    <div class="url-line">www.legacyplanner.org</div>
    <p class="lead">In 20 minutes you can have a legal will – for free</p>
    <div class="contact-band">
      <div class="contact-band__head">CONTACT US</div>
      <h4>HAVE MORE QUESTION?</h4>
      <p style="text-align:center">Contact our office for further details.</p>
      <div class="contact-row"><span class="icon"><svg width="13" height="13" viewBox="0 0 24 24" fill="#fff"><path d="M6.6 10.8a15 15 0 0 0 6.6 6.6l2.2-2.2c.3-.3.7-.4 1-.2 1.1.4 2.3.6 3.6.6.6 0 1 .4 1 1V20c0 .6-.4 1-1 1A17 17 0 0 1 3 4c0-.6.4-1 1-1h3.5c.6 0 1 .4 1 1 0 1.3.2 2.5.6 3.6.1.3 0 .7-.2 1z"/></svg></span>(555) 014-2290</div>
      <div class="contact-row"><span class="icon"><svg width="13" height="13" viewBox="0 0 24 24" fill="#fff"><path d="M2 5h20v14H2z" opacity=".0"/><path d="M3 5h18v14H3zm2 2v.5l7 4.5 7-4.5V7z"/></svg></span>giving@maasinc.org</div>
      <div class="contact-row"><span class="icon"><svg width="13" height="13" viewBox="0 0 24 24" fill="#fff"><path d="M12 2a7 7 0 0 0-7 7c0 5 7 13 7 13s7-8 7-13a7 7 0 0 0-7-7zm0 9.5A2.5 2.5 0 1 1 12 6a2.5 2.5 0 0 1 0 5.5z"/></svg></span>410 Lantern Row, Suite 12, Fairhaven</div>
      <div class="follow">Follow us</div>
      <div class="social"><span></span><span></span><span></span></div>
    </div>
  </article>

  <article class="panel panel--cover">
    <h1 class="cover-title">TRANSFORM <span>YOUR GIVING</span></h1>
    <div class="cover-rule"></div>
    <h2 class="cover-strap">BE STRATEGIC<br><span>BE SMART</span></h2>
    <p class="cover-sub">Discover the Impact of Smart Giving with Meadowlark and Allied Services</p>
    <div class="cover-photo" role="img" aria-label="Caregiver embracing an older woman outdoors"></div>
    <div class="cover-foot">
      <div class="brand"><span class="brand__mark"></span><span class="brand__name">MAAS</span></div>
      <p class="brand__sub">Meadowlark and Allied Services</p>
      <div class="web">www.maasinc.org</div>
    </div>
  </article>
</section>

<!-- Inside of the brochure -->
<section class="spread spread--inside">
  <article class="panel panel--stocks">
    <div class="corner corner--tl"></div>
    <p style="margin-top:24px">We would like to introduce you to five strategic and smart ways to give that could potentially be more beneficial to you compared to traditional cash giving.</p>
    <p>We encourage you to keep this information as a guide as you plan your giving.</p>
    <div class="topic"><span class="badge"></span><h3>GIFTS OF STOCKS OR APPRECIATED ASSETS<small>STRATEGIC &amp; SMART</small></h3></div>
    <p>Consider your long-term publicly traded stock as a way to give to our favorite charity.</p>
    <p>Your donation's significantly bigger impact when you donate long-term appreciated securities, including stock or mutual funds, and more directly to your favorite cause.</p>
    <h4 class="how">HOW DOES IT WORK?</h4>
    <p>When you donate stock to a charity, you will generally take a tax deduction for the full market value. Because you are not donating cash, your contribution can be adjusted at a significantly higher value, minimizing the tax due later.</p>
    <div class="photo photo--walk" role="img" aria-label="Caregiver walking arm in arm with an older woman"></div>
  </article>

  <article class="panel panel--navy panel--funds">
    <div class="topic"><span class="badge"></span><h3>DONOR-ADVISED FUND (DAF)<small>STRATEGIC &amp; SMART</small></h3></div>
    <p>Consider a DAF – a simple, flexible and tax-advantaged way to give to our cause.</p>
    <p>A Donor Advised Fund is an account set up by a sponsoring organization. It lets you contribute assets, receive an immediate tax deduction and recommend grants over time.</p>
    <h4 class="how">HOW DOES IT WORK?</h4>
    <p>You establish a DAF and contribute cash, stocks or non-public assets. You may be eligible for an immediate tax deduction. Assets grow tax-free while you decide which charities to support.</p>
    <div class="divider"></div>
    <div class="topic"><span class="badge"></span><h3>QUALIFIED CHARITABLE DISTRIBUTION (QCD)<small>STRATEGIC &amp; SMART</small></h3></div>
    <p>If you are 70½ or older, consider giving directly from your IRA to support our work and lower your taxable income this year.</p>
    <h4 class="how">HOW DOES IT WORK?</h4>
    <p>You may transfer up to the annual limit from your IRA straight to a qualified charity. The gift counts toward your required minimum distribution and is not added to your income.</p>
    <div class="web-foot">www.maasinc.org</div>
  </article>

  <article class="panel panel--crypto">
    <div class="topic"><span class="badge"></span><h3>CRYPTOCURRENCY<small>STRATEGIC &amp; SMART</small></h3></div>
    <p>Consider donating Bitcoin and other cryptocurrencies to your favorite charity. Gifts of digital assets held over a year may offer valuable tax savings.</p>
    <h4 class="how">HOW DOES IT WORK?</h4>
    <ul class="ticks">
      <li>Your tax deduction will be equal to the fair market value of the asset at the time of the gift.</li>
      <li>Crypto is treated as property, so no capital gains tax is due.</li>
      <li>Transfers are simple and secure through our giving partner.</li>
    </ul>
    <div class="topic"><span class="badge"></span><h3>CHARITABLE GIFT ANNUITY<small>STRATEGIC &amp; SMART</small></h3></div>
    <p>Consider establishing a charitable gift annuity to give and receive.</p>
    <h4 class="how">HOW DOES IT WORK?</h4>
    <p>A charitable gift annuity is a contract between you and the charity. In exchange for your gift, you receive fixed payments for life, with part of the gift becoming a lasting donation.</p>
    <div class="brand-foot">
      <div class="brand"><span class="brand__mark"></span><span class="brand__name">MAAS</span></div>
      <p class="brand__sub" style="color:var(--navy)">Meadowlark and Allied Services</p>
    </div>
  </article>
</section>

</body>
</html>
```